I have a logo and need to design the business card and stationery.
Updates

The uploaded logo image named as GREYMARSH CONSTRUCTION which is to be replaced to GREYMARSH CONTRACTS. Kindly add below details and submit the designs- Company name- Greymarsh Engineering Contracts LLP Name & Post- Kelvan Joshi (Designated Partner) Address- Block No.317, Wing C, Tulvo Trade Court, Manek Pural Road, Ruparel Industrial Estate, Goregaon(E), Mumbai - 400 063 Contact- +91 97415 60382 Email- kelvanjoshi@mailbrook.example Website- www.greymarshcontracts.example Contact for Letterhead- +91-22-28754193

Hi Tovin Rahul, We are liking your Design #28860835. We have suggested some changes which are mentioned in feedback. Kindly revert with it asap to finalize this design.

Colors

Designer to choose colors to be used in the design.

```html
<!DOCTYPE html>
<html lang="en">
<head>
<meta charset="utf-8">
<title>Greymarsh Contracts Letterhead</title>
<link rel="stylesheet" href="https://fonts.googleapis.com/css2?family=Arimo:wght@400&family=Mulish:wght@700;800&display=swap">
<style>
  :root {
    --backdrop: #d9d9d9;
    --paper: #fbfbfc;
    --ink-dark: #333333;
    --ink-body: #555555;
    --ink-muted: #666666;
    --rule: #5a5a5a;
    --mark-tint: #f1f2f4;
    --sign-tint: #e6e6e8;
  }
  * { margin: 0; padding: 0; box-sizing: border-box; }
  html, body {
    width: 1200px; height: 1079px; overflow: hidden;
    background: var(--backdrop);
  }
  .letterhead {
    position: absolute; left: 268px; top: 70px;
    width: 664px; height: 940px;
    background: var(--paper);
    font-family: "Arimo", Arial, sans-serif;
  }
  .brand {
    position: absolute; left: 0; top: 41px; width: 100%;
    display: flex; flex-direction: column; align-items: center;
  }
  .brand-square {
    width: 47px; height: 47px; border: 5px solid var(--ink-dark);
  }
  .brand-name {
    margin-top: 12px;
    font-family: "Mulish", sans-serif; font-weight: 800;
    font-size: 14px; letter-spacing: 1.5px; color: var(--ink-dark);
  }
  .bg-mark {
    position: absolute; left: 181px; top: 320px;
    width: 302px; height: 302px; background: var(--mark-tint);
  }
  .salutation {
    position: absolute; left: 60px; top: 290px;
    font-family: "Mulish", sans-serif; font-weight: 700;
    font-size: 15.5px; color: #4a4a4a;
  }
  .body-copy {
    position: absolute; left: 59px; top: 333px; width: 546px;
    font-size: 10.7px; line-height: 13.6px; color: var(--ink-body);
  }
  .body-copy p { margin-bottom: 12.4px; }
  .closing {
    position: absolute; left: 60px; top: 614px;
    font-family: "Mulish", sans-serif; font-weight: 700;
    font-size: 8.6px; color: #444;
  }
  .signature {
    position: absolute; left: 60px; top: 653px;
    width: 109px; height: 34px; background: var(--sign-tint);
  }
  .footer-rule {
    position: absolute; left: 59px; top: 860px;
    width: 546px; height: 1px; background: var(--rule);
  }
  .contact-list, .address {
    position: absolute; top: 867px;
    font-size: 10px; line-height: 14.4px; color: var(--ink-muted);
    list-style: none;
  }
  .contact-list { left: 59px; }
  .contact-list li { display: flex; align-items: center; gap: 6px; }
  .contact-list svg { width: 8px; height: 8px; fill: var(--ink-dark); }
  .address { right: 59px; text-align: right; font-style: normal; }
</style>
</head>
<body>
<main class="letterhead">
  <header class="brand">
    <div class="brand-square"></div>
    <div class="brand-name">GREYMARSH CONTRACTS</div>
  </header>

  <div class="bg-mark" aria-hidden="true"></div>

  <h1 class="salutation">Dear Mr. Smith,</h1>

  <section class="body-copy">
    <p>Lorem ipsum dolor sit amet, consectetuer adipiscing elit, sed diam nonmmy nibh euismod tincidunt ut laor eet dolore magna aliquam erat volutpat. Ut wisi enim ad minim veniam, quis nostrud exerci tationmcorper suscipit lobortis nisl ut aliquip ex ea commodo consequat. Duis autem vel eum iriure dolor in hendrerit in vulputate velit esse molestie consequat, vel illum dolore eu feugiat</p>
    <p>Rorem ipsum dolor sit amet, consectetuer adipiscing elit, sed diam nonmmy nibh euismod tincidunt ut laor eet dolore magna aliquam erat volutpat. Ut wisi enim ad minim veniam, quis nostrud exerci tationmcorper suscipit lobortis nisl ut aliquip ex ea commodo consequat. Duis autem vel eum iriure dolor in hendrerit in vulputate velit esse molest</p>
    <p>Dorem ipsum dolor sit amet, consectetuer adipiscing elit, sed diam nonmmy nibh euismod tincidunt ut laor eet dolore magna aliquam erat volutpat. Ut wisi enim ad minim veniam, quis nostrud exerci tationmcorper suscipit lobortis nisl ut aliquip ex ea commodo consequat. Duis autem vel eum iriure dolor in hendrerit in suscipit lobortis nisl ut aliquip ex ea commodo consequat. Duis autem vel eum iriure dolor in hendrerit in vulputate velit esse molestie consequat, vel illum</p>
    <p>Sorem ipsum dolor sit amet, consectetuer adipiscing elit, sed diam nonmmy nibh euismod tincidunt ut laor eet dolore magna aliquam erat volutpat. Ut wisi enim ad minim veniam, quis nostrud exerci tationmcorper suscipit lobortis nisl ut aliquip ex ea commodo consequat. Duis autem vel eum iriure dolor in</p>
  </section>

  <div class="closing">Sincerely,</div>
  <div class="signature" role="img" aria-label="Handwritten signature"></div>

  <div class="footer-rule"></div>
  <ul class="contact-list">
    <li><svg viewBox="0 0 10 10"><path d="M2 0.5 L3.8 2.6 L2.9 3.7 Q4 5.9 6.3 7.1 L7.4 6.2 L9.5 8 L8.2 9.5 Q1 8 0.5 1.8 Z"/></svg>+91-22-28754193</li>
    <li><svg viewBox="0 0 10 10"><path d="M0 2 H10 V8.5 H0 Z M0.6 2.4 L5 5.8 L9.4 2.4" stroke="#fbfbfc" stroke-width="0.8"/></svg>kelvanjoshi@mailbrook.example</li>
    <li><svg viewBox="0 0 10 10"><circle cx="5" cy="5" r="4.6"/><path d="M0.6 5 H9.4 M5 0.4 V9.6" stroke="#fbfbfc" stroke-width="0.8"/></svg>www.greymarshcontracts.example</li>
  </ul>
  <address class="address">
    Block No.317, Wing C, Tulvo Trade Court<br>
    Manek Pural Road, Ruparel Industrial Estate<br>
    Goregaon(E), Mumbai - 400 063
  </address>
</main>
</body>
</html>
```